Profesional personal website needs design and business card

I need a business card with my professional name as a logo "Dorian Vitality" for my business. I am a Wellness Coach, consultant and trainer. So it should be professional, wellness oriented and modern.

Target Market(s)

Private clients, governments, corporations. Luxury and high market.

Industry/Entity Type

Health And Wellness

Contact Information for Business Card

Dorian Vitality should be the logo

Colors

Designer to choose colors to be used in the design.

Requirements
Must have
• Dorian Vitality
• Name: Tomás Lirandel
• Wellness Coach, Consultant & Trainer.
• Website: www.dorianvitality-example.com
• Phone:
• Spain (+34) 612 480 317
• (USA) +1 (555) 610 4829
Nice to have
• The most important is the design of "Dorian Vitality", as this is going to be my personal brand logo. It should be professional, wellness, high end and actual.
Should not have
• no golds, no baroque style..

```html
<!DOCTYPE html>
<html lang="en">
<head>
<meta charset="utf-8">
<title>Dorian Vitality – Business Card</title>
<link rel="stylesheet" href="https://fonts.googleapis.com/css2?family=Montserrat:wght@400;500;700;800&display=swap">
<style>
  :root {
    --brand-blue: #1b22a8;
    --brand-blue-deep: #141a8c;
    --brand-yellow: #f5b70a;
    --ink: #1e2340;
    --paper: #ffffff;
    --backdrop: #2b2b2d;
  }
  * { box-sizing: border-box; margin: 0; padding: 0; }
  html, body { width: 1200px; height: 930px; overflow: hidden; }
  body {
    background: var(--backdrop);
    font-family: "Montserrat", sans-serif;
    position: relative;
  }
  .card {
    position: absolute;
    left: 250px;
    width: 700px;
    height: 400px;
    border-radius: 22px;
    overflow: hidden;
  }
  .card--back {
    top: 45px;
    background: var(--brand-blue);
    display: flex;
    align-items: center;
    justify-content: center;
  }
  .card--front { top: 485px; background: var(--paper); }

  .wordmark {
    font-weight: 800;
    text-transform: uppercase;
    letter-spacing: 2px;
    line-height: 1;
  }
  .card--back .wordmark { color: var(--paper); font-size: 48px; }
  .card--front .wordmark {
    position: absolute;
    left: 30px;
    top: 205px;
    width: 250px;
    text-align: center;
    color: var(--brand-blue);
    font-size: 30px;
  }

  .divider {
    position: absolute;
    left: 300px;
    top: 80px;
    width: 2px;
    height: 200px;
    background: var(--brand-blue);
  }

  .contact {
    position: absolute;
    left: 328px;
    top: 50px;
    color: var(--ink);
  }
  .contact__name {
    font-size: 26px;
    font-weight: 700;
    text-transform: uppercase;
    color: var(--brand-blue);
    letter-spacing: 0.5px;
  }
  .contact__name .surname { color: var(--brand-yellow); }
  .contact__role { font-size: 14px; line-height: 1.35; margin-top: 4px; }
  .contact__address { font-size: 15px; line-height: 1.35; margin-top: 14px; }
  .contact__list { list-style: none; margin-top: 12px; font-size: 15px; line-height: 1.5; }
  .contact__list li { display: flex; align-items: center; gap: 9px; }
  .contact__list svg { width: 13px; height: 13px; flex: none; }
  .contact__list .highlight { color: var(--brand-yellow); }

  .flag { display: inline-block; width: 22px; height: 14px; margin-left: 14px; }

  .card__band { position: absolute; left: 0; bottom: 0; width: 700px; height: 400px; }
</style>
</head>
<body>

  <section class="card card--back">
    <span class="wordmark">Dorian Vitality</span>
  </section>

  <section class="card card--front">
    <svg class="card__band" viewBox="0 0 700 400" aria-hidden="true">
      <path d="M0 400 L0 392 L430 362 C470 359 480 318 520 316 L700 304 L700 400 Z" fill="var(--brand-blue)"/>
      <path d="M0 378 L440 346" stroke="var(--brand-yellow)" stroke-width="6" fill="none"/>
    </svg>

    <span class="wordmark">Dorian Vitality</span>
    <div class="divider"></div>

    <div class="contact">
      <h1 class="contact__name">Tomás <span class="surname">Lirandel</span></h1>
      <p class="contact__role">Wellness Coach,<br>Consultant &amp; Trainer.</p>
      <p class="contact__address">418 Marlow Ave<br>Fernhill, BC, V0X 3K7</p>
      <ul class="contact__list">
        <li>
          <svg viewBox="0 0 24 24"><path d="M6.6 10.8a15 15 0 0 0 6.6 6.6l2.2-2.2a1 1 0 0 1 1-.25 11.4 11.4 0 0 0 3.6.57 1 1 0 0 1 1 1V20a1 1 0 0 1-1 1A17 17 0 0 1 3 4a1 1 0 0 1 1-1h3.5a1 1 0 0 1 1 1c0 1.25.2 2.45.57 3.57a1 1 0 0 1-.25 1z" fill="var(--brand-blue)"/></svg>
          (+34) 612 480 317
          <svg class="flag" viewBox="0 0 22 14"><rect width="22" height="14" fill="#c60b1e"/><rect y="3.5" width="22" height="7" fill="#ffc400"/></svg>
        </li>
        <li>
          <svg viewBox="0 0 24 24"><rect x="6" y="2" width="12" height="20" rx="2" fill="none" stroke="var(--brand-blue)" stroke-width="2.4"/><circle cx="12" cy="18" r="1.3" fill="var(--brand-blue)"/></svg>
          +1 (555) 610 4829
          <svg class="flag" viewBox="0 0 22 14"><rect width="22" height="14" fill="#fff"/><g fill="#b22234"><rect width="22" height="2"/><rect y="4" width="22" height="2"/><rect y="8" width="22" height="2"/><rect y="12" width="22" height="2"/></g><rect width="10" height="7" fill="#3c3b6e"/></svg>
        </li>
        <li>
          <svg viewBox="0 0 24 24"><rect x="2" y="5" width="20" height="14" rx="1.5" fill="none" stroke="var(--brand-blue)" stroke-width="2.2"/><path d="M3 6l9 7 9-7" fill="none" stroke="var(--brand-blue)" stroke-width="2.2"/></svg>
          info@dorianvitality-example.com
        </li>
        <li>
          <svg viewBox="0 0 24 24"><circle cx="12" cy="12" r="10" fill="var(--brand-blue)"/><path d="M2 12h20M12 2c3 3 3 17 0 20M12 2c-3 3-3 17 0 20" stroke="#fff" stroke-width="1.4" fill="none"/></svg>
          <span>www.<span class="highlight">dorianvitality-example</span>.com</span>
        </li>
      </ul>
    </div>
  </section>

</body>
</html>
```